I need a business card design for a real estate finance, development and management business. We deal with high net worth clients and ask that the business card be neat, clean and sophisticated. We like the attached logo design, font and color and want to incorporate all this into the business card.

Industry/Entity Type

Real Estate

```html
<!DOCTYPE html>
<html lang="en">
<head>
<meta charset="utf-8">
<title>Silver Harbor – Business Card</title>
<link rel="stylesheet" href="https://fonts.googleapis.com/css2?family=Open+Sans:wght@400;700&display=swap">
<style>
  :root {
    --page: #e4e4e4;
    --card: #ffffff;
    --brand-blue: #1f5b9c;
    --ink-blue: #24609f;
    --card-shadow: rgba(0, 0, 0, 0.18);
  }
  * { box-sizing: border-box; margin: 0; padding: 0; }
  html, body {
    width: 1200px;
    height: 947px;
    overflow: hidden;
    background: var(--page);
    font-family: "Open Sans", Arial, sans-serif;
    color: var(--ink-blue);
  }
  .canvas {
    position: relative;
    width: 1200px;
    height: 947px;
  }
  .card {
    position: absolute;
    top: 323px;
    width: 525px;
    height: 300px;
    background: var(--card);
    box-shadow: 0 6px 18px var(--card-shadow);
    overflow: hidden;
  }
  .card--front { left: 50px; }
  .card--back { left: 625px; }

  /* brand lockup */
  .brand {
    position: absolute;
    text-align: center;
    color: var(--brand-blue);
  }
  .brand__name {
    display: block;
    font-weight: 400;
    font-size: 36px;
    letter-spacing: 2px;
    text-transform: uppercase;
    line-height: 1;
    white-space: nowrap;
  }
  .brand__tagline {
    display: block;
    margin-top: 8px;
    font-size: 8px;
    letter-spacing: 2px;
    text-transform: uppercase;
    word-spacing: 8px;
    white-space: nowrap;
  }
  .card--front .brand { left: 175px; top: 50px; width: 320px; }
  .card--front .brand__name { font-size: 30px; }
  .card--front .brand__tagline { font-size: 7px; }
  .card--back .brand { left: 0; right: 0; top: 118px; }

  /* back card bands */
  .band {
    position: absolute;
    left: 0;
    right: 0;
    height: 20px;
    background: var(--brand-blue);
  }
  .band--top { top: 0; }
  .band--bottom { bottom: 0; }

  /* front card divider */
  .rule {
    position: absolute;
    left: 0;
    top: 192px;
    width: 525px;
    height: 2px;
    background: var(--brand-blue);
  }

  /* contact blocks */
  .contact {
    position: absolute;
    font-size: 14px;
    line-height: 1.25;
    color: var(--ink-blue);
  }
  .contact svg {
    display: block;
    width: 18px;
    height: 18px;
    margin-bottom: 4px;
    fill: var(--ink-blue);
  }
  .contact--mobile {
    top: 160px;
    left: 22px;
    display: flex;
    align-items: center;
    gap: 10px;
  }
  .contact--mobile svg { margin-bottom: 0; }
  .contact--address { top: 204px; left: 22px; width: 150px; }
  .contact--phone { top: 204px; left: 195px; }
  .contact--email { top: 204px; left: 330px; }
  .holder-name {
    position: absolute;
    right: 24px;
    top: 160px;
    font-size: 18px;
    line-height: 1.2;
    letter-spacing: 0.5px;
    color: var(--ink-blue);
  }
  .holder-name strong { font-weight: 700; }
</style>
</head>
<body>
<main class="canvas">

  <!-- front: contact side -->
  <section class="card card--front" aria-label="Business card, contact side">
    <div class="brand">
      <span class="brand__name">Silver Harbor</span>
      <span class="brand__tagline">Capital Development Management</span>
    </div>

    <div class="contact contact--mobile">
      <svg viewBox="0 0 24 24" aria-hidden="true"><path d="M7 1h10a2 2 0 0 1 2 2v18a2 2 0 0 1-2 2H7a2 2 0 0 1-2-2V3a2 2 0 0 1 2-2zm0 3v14h10V4H7zm5 15.5a1.2 1.2 0 1 0 0 2.4 1.2 1.2 0 0 0 0-2.4z"/></svg>
      <span>+0000 1234 5679</span>
    </div>

    <div class="holder-name">YOUR<strong>NAME</strong></div>

    <div class="rule"></div>

    <div class="contact contact--address">
      <svg viewBox="0 0 24 24" aria-hidden="true"><path d="M12 3 1 12h3v9h6v-6h4v6h6v-9h3z"/></svg>
      <span>Your Local or business address.</span>
    </div>

    <div class="contact contact--phone">
      <svg viewBox="0 0 24 24" aria-hidden="true"><path d="M3 8c0-2 3-4 9-4s9 2 9 4v2h-5V8H8v2H3zm3 4h12l3 8H3zm6 2a2.5 2.5 0 1 0 0 5 2.5 2.5 0 0 0 0-5z"/></svg>
      <span>+000 1234 5679</span><br>
      <span>+000 1234 5679</span>
    </div>

    <div class="contact contact--email">
      <svg viewBox="0 0 24 24" aria-hidden="true"><path d="M2 4h20v13H8l-5 4v-4H2z"/></svg>
      <span>name@yourwebsite.com</span><br>
      <span>www.yourwebsite.com</span>
    </div>
  </section>

  <!-- back: brand side -->
  <section class="card card--back" aria-label="Business card, brand side">
    <div class="band band--top"></div>
    <div class="brand">
      <span class="brand__name">Silver Harbor</span>
      <span class="brand__tagline">Capital Development Management</span>
    </div>
    <div class="band band--bottom"></div>
  </section>

</main>
</body>
</html>
```